Unique Builder wordpress website - Supply Graphics Only

We need a brand new website for a building company in Perth, Australia who constructs insulated panels (sip).
What is a SIP?
A SIP is a high-performance building panel used for floors, walls, and roofs in residential and commercial buildings. Panels are typically made using Expanded Polystyrene (EPS) sandwiched between two structural skins.
The design must incorporate a slick professional look and keep to the logo colours (Lime green & Blacks). The logo must not change colours or be altered. (
We will convert the graphics to a wordpress site. We have our own coders)
Design:
The website design must be clean, mobile friendly and the final design will be adapted to WordPress CMS.
The menus must contain dropdown menus and front page may contain a youtube video at a later date.
Fonts must be clear and easy to read
The contact us page will need to have an online form and google map.
The 16 pages listed will be the complete site and are for reference only. For this project the winning designer would need to supply the Homepage, and 1 inner pages only as PSD files.
The structure is as follows:
Home
About us
Marlow Fen Dwellings
What is a sip
Benefits
FAQ
Designs
Residential
Granny Flats
Architectural design
Photo Gallery <--- Would be great if a sample design can be provided
Services
Project management and custom design
Site Assembly
Kit Supply
Contact us
***We don't need the designer to design every page however a 1 inner page would be ideal****
Our Competitors websites
Note: the following websites look crap however, the following websites are some of our competitors. We want a clean and awesome layout.
http://www.corvamoda.com.au/
http://dralventorix.com.au/
http://www.quilbarrow.net.au/
New home builders and commercial builders
Building
5+ page

```html
<!DOCTYPE html>
<html lang="en">
<head>
<meta charset="utf-8">
<title>Kestrane Panels – Home</title>
<link href="https://fonts.googleapis.com/css2?family=Ubuntu:wght@400;500;700&family=Lato:wght@400;700&display=swap" rel="stylesheet">
<style>
:root{
  --lime:#9cc42c;
  --lime-dark:#86ab1f;
  --ink:#1e1e1e;
  --charcoal:#2b2b2b;
  --card:#333333;
  --text:#5a5a5a;
  --muted:#999999;
  --line:#dddddd;
  --white:#ffffff;
}
*{margin:0;padding:0;box-sizing:border-box}
html,body{width:1200px;height:2687px;overflow:hidden}
body{font-family:"Lato",sans-serif;color:var(--text);background:var(--white);position:relative}
.wrap{width:1004px;margin:0 auto;position:relative}

/* top bar */
.topbar{height:30px;background:var(--ink);color:#ddd;font-size:11px}
.topbar .wrap{display:flex;justify-content:space-between;align-items:center;height:30px}
.topbar .phone{display:flex;align-items:center;gap:8px;font-family:"Ubuntu",sans-serif;font-weight:700;font-size:14px;color:#fff}
.topbar nav{display:flex;gap:22px}

/* header */
.header{height:99px;background:linear-gradient(#fff,#f3f3f3);border-bottom:1px solid #e6e6e6}
.header .wrap{display:flex;justify-content:space-between;align-items:stretch;height:99px}
.brand{display:flex;align-items:center;gap:14px}
.brand-mark{width:40px;height:40px;background:var(--ink);border-radius:4px}
.brand-name{font-family:"Ubuntu",sans-serif;font-weight:500;font-size:34px;color:var(--ink);line-height:1}
.brand-sub{font-size:9px;letter-spacing:1px;color:var(--ink);margin-top:4px;text-transform:uppercase}
.mainnav{display:flex;align-items:stretch;font-size:13px;color:#333;margin-right:-8px}
.mainnav a{display:flex;align-items:center;padding:0 17px}
.mainnav a.active{background:var(--lime);color:#fff;font-weight:700;padding:0 22px}

/* hero */
.hero{height:501px;position:relative;overflow:hidden;
  background:
    radial-gradient(ellipse 40% 30% at 88% 8%,rgba(150,185,220,.95),rgba(150,185,220,0) 70%),
    radial-gradient(ellipse 30% 35% at 92% 55%,rgba(150,125,95,.7),rgba(150,125,95,0) 70%),
    radial-gradient(ellipse 60% 45% at 45% 40%,rgba(242,204,128,.9),rgba(242,204,128,0) 75%),
    radial-gradient(ellipse 70% 40% at 40% 95%,rgba(120,80,40,.8),rgba(120,80,40,0) 80%),
    linear-gradient(180deg,#c9c4b6 0%,#e2bd7a 22%,#d7a65a 50%,#b98545 75%,#8c6134 100%)}
.hero-caption{position:absolute;left:88px;top:208px;width:432px;padding:12px 14px;background:rgba(40,40,40,.7);color:#fff;font-family:"Ubuntu",sans-serif;font-weight:700;font-size:21px;line-height:33px}

/* section heading */
.heading{font-family:"Ubuntu",sans-serif;font-weight:500;font-size:32px;color:var(--ink)}
.heading .hl{color:var(--lime)}
.divider{display:flex;align-items:center;gap:6px;margin-top:12px}
.divider i{display:block;height:2px;width:96px;background:var(--line)}
.divider b{width:16px;height:16px;background:var(--ink);transform:rotate(45deg) scaleY(.6);border:2px solid var(--lime)}
.center{text-align:center}
.center .divider{justify-content:center}

/* about */
.about{height:332px}
.about .wrap{display:flex;padding-top:38px}
.about-copy{width:590px;padding-right:24px;border-right:1px solid #e3e3e3;height:250px}
.about-copy .divider{justify-content:flex-start;margin-top:6px}
.about-copy .divider i{display:none}
.about-copy p{font-size:12.5px;line-height:21.5px;margin-top:8px;color:var(--text)}
.btn{display:inline-block;background:var(--charcoal);color:#fff;font-size:12px;font-weight:700;padding:6px 12px;margin-top:16px}
.video{margin-left:auto;margin-top:4px;width:366px;height:224px;position:relative;box-shadow:0 10px 14px -8px rgba(0,0,0,.5);
  background:
    radial-gradient(ellipse 35% 45% at 30% 30%,rgba(230,225,215,.6),rgba(230,225,215,0) 70%),
    radial-gradient(ellipse 30% 40% at 75% 55%,rgba(70,90,130,.55),rgba(70,90,130,0) 70%),
    linear-gradient(180deg,#8c877e 0%,#bdb6aa 45%,#7a6a55 100%)}
.video .play{position:absolute;left:167px;top:84px}
.video .controls{position:absolute;left:0;right:0;bottom:0;height:20px;background:#222;display:flex;align-items:center;gap:8px;padding:0 8px;font-size:8px;color:#ccc}
.video .sq{width:16px;height:11px;background:var(--lime)}
.video .track{flex:1;height:4px;background:#555;position:relative}
.video .track i{position:absolute;left:0;top:0;height:4px;width:20%;background:var(--lime)}

/* benefits */
.benefits{height:430px;position:relative;
  background:
    radial-gradient(ellipse 30% 50% at 12% 20%,rgba(150,140,120,.35),rgba(150,140,120,0) 70%),
    radial-gradient(ellipse 30% 40% at 88% 15%,rgba(200,200,200,.25),rgba(200,200,200,0) 70%),
    linear-gradient(180deg,#5b5c5e,#3f4042 60%,#4a4b4d)}
.benefits .heading{color:#fff;padding-top:30px}
.benefits .divider i{background:#888}
.cards{display:flex;gap:14px;margin-top:10px}
.card{width:240px;background:var(--card)}
.card .pic{height:163px}
.card h3{font-family:"Ubuntu",sans-serif;font-weight:700;font-size:15px;color:var(--lime);text-align:center;margin-top:10px}
.card p{font-size:11px;line-height:16px;color:#ccc;text-align:center;padding:4px 12px 0}
.card .more{display:block;text-align:center;font-size:11.5px;font-weight:700;color:#fff;margin:6px 0 14px}
.arrow{position:absolute;top:240px}
.arrow.l{left:56px}.arrow.r{right:56px}

/* gallery */
.gallery-head{height:163px;padding-top:36px}
.grid{display:grid;grid-template-columns:repeat(4,300px);grid-auto-rows:205px}

/* testimonials */
.testimonials{height:396px;padding-top:36px}
.avatars{display:flex;justify-content:center;gap:15px;margin-top:18px}
.avatar{width:104px;height:104px;border-radius:50%;border:4px solid #e2e2e2}
.quote{margin:20px auto 0;width:900px;text-align:center;font-size:13px;line-height:22px;color:#444}
.quote-mark{display:block;margin:0 auto 10px}
.author{color:var(--lime);font-size:12px;font-weight:700;margin-top:14px;text-align:center}

/* footer */
.footer{height:277px;background:linear-gradient(180deg,#151515,#222)}
.footer .wrap{display:flex;padding-top:30px}
.footer h4{font-family:"Ubuntu",sans-serif;font-weight:400;font-size:17px;color:#fff;padding-bottom:8px;border-bottom:1px solid #444}
.col-links{width:395px}
.link-cols{display:flex;gap:30px;margin-top:10px}
.link-cols ul{list-style:none;font-size:11.5px;color:#ccc;line-height:23px;width:130px}
.link-cols ul:last-child{width:230px}
.link-cols li::before{content:"›";color:#fff;margin-right:8px;font-weight:700}
.link-cols li.current{color:#fff;font-weight:700}
.col-contact{width:230px;margin-left:100px}
.contact-list{list-style:none;margin-top:16px;font-size:12px;color:#ccc}
.contact-list li{display:flex;gap:14px;margin-bottom:20px;line-height:16px}
.contact-list svg{flex:none}
.col-form{width:222px;margin-left:57px}
.form{margin-top:12px;display:flex;flex-direction:column;gap:6px}
.field{height:25px;background:#fff;font-size:11px;color:#555;display:flex;align-items:center;gap:8px;padding:0 8px}
.field.tall{height:48px;align-items:flex-start;padding-top:6px}
.submit{width:86px;height:27px;background:var(--lime);color:#fff;font-weight:700;font-size:12px;display:flex;align-items:center;justify-content:center;margin-top:8px}

.bottombar{height:49px;background:#2a2a2a}
.bottombar .wrap{display:flex;justify-content:space-between;align-items:center;height:49px;font-size:11px;color:#ccc}
.social{display:flex;gap:9px}
.social-btn{width:28px;height:28px;border-radius:50%;background:#e9e9e9;box-shadow:inset 0 0 0 7px #e9e9e9,inset 0 0 0 14px #3a3a3a;display:block}
</style>
</head>
<body>

<div class="topbar">
  <div class="wrap">
    <div class="phone">
      <svg width="14" height="14" viewBox="0 0 24 24"><path fill="#9cc42c" d="M6.6 10.8a15 15 0 0 0 6.6 6.6l2.2-2.2c.3-.3.7-.4 1-.2 1.1.4 2.3.6 3.6.6.6 0 1 .4 1 1V20c0 .6-.4 1-1 1A17 17 0 0 1 3 4c0-.6.4-1 1-1h3.5c.6 0 1 .4 1 1 0 1.3.2 2.5.6 3.6.1.3 0 .7-.2 1z"/></svg>
      123-456-7890
    </div>
    <nav>
      <a>Granny Flats</a><a>Residential</a><a>Photo Gallery</a><a>Project management and custom design</a><a>Services</a><a>Site Assembly</a><a>Kit Supply</a><a>Contact us</a>
    </nav>
  </div>
</div>

<header class="header">
  <div class="wrap">
    <div class="brand">
      <span class="brand-mark"></span>
      <div>
        <div class="brand-name">Kestrane Panels</div>
        <div class="brand-sub">Advanced Building Technology</div>
      </div>
    </div>
    <nav class="mainnav">
      <a class="active">Home</a><a>About us</a><a>Marlow Fen Dwellings</a><a>What is a sip</a><a>Benefits</a><a>FAQs</a><a>Designs</a>
    </nav>
  </div>
</header>

<section class="hero" role="img" aria-label="Photo of stacked insulated building panels on a site under a blue sky">
  <div class="hero-caption">We Offer A Unique Design And Project Delivery Service To Develop Your Specific Building Requirements.</div>
</section>

<section class="about">
  <div class="wrap">
    <div class="about-copy">
      <h2 class="heading"><span class="hl">About To</span> Kestrane Panels</h2>
      <div class="divider"><b></b></div>
      <p>Lorem ipsum dolor sit amet, consectetuer adipiscing elit, sed diam nonummy nh euismodl tincidunt ut laoreet dolore magna aliquam erat volutpat. Ut wisi enim ad minim venia quisl nostrud exerci tation ullamcorper suscipit lobortis nisl ut aliquip ex ea comm consequat.a Duis autem vel eum iriure dolor in hendrerit in vulputate velit esse molestie consequat vel illum dolore eu feugiat nulla facilisis at vero eros duis dolore te feugait nulla fac hendrerit in vulputate velit esse molestie.</p>
      <a class="btn">Read More</a>
    </div>
    <div class="video" role="img" aria-label="Video still of two workers assembling panels on a floor">
      <svg class="play" width="32" height="40" viewBox="0 0 32 40"><path d="M0 0 L32 20 L0 40Z" fill="#fff"/></svg>
      <div class="controls"><span class="sq"></span><span class="track"><i></i></span><span>1:47 / 12:05</span><span class="sq"></span><span class="sq"></span></div>
    </div>
  </div>
</section>

<section class="benefits" role="region" aria-label="Our Benefits">
  <div class="wrap">
    <div class="center">
      <h2 class="heading">Our Benefits</h2>
      <div class="divider"><i></i><b></b><i></i></div>
    </div>
    <div class="cards">
      <div class="card">
        <div class="pic" role="img" aria-label="Builder in hard hat working at a laptop" style="background:radial-gradient(ellipse 40% 40% at 45% 30%,rgba(240,200,40,.8),rgba(240,200,40,0) 70%),radial-gradient(ellipse 45% 40% at 40% 70%,rgba(70,100,150,.7),rgba(70,100,150,0) 70%),linear-gradient(135deg,#eee9de,#d8cdb6 60%,#b9b3a6)"></div>
        <h3>Excellent Service</h3>
        <p>Lorem ipsum dolor sit amet, consectetuer adipiscing elit, sed diam nonummy ni tincidunt ut laoreet dolore magna</p>
        <a class="more">Read More &gt;&gt;</a>
      </div>
      <div class="card">
        <div class="pic" role="img" aria-label="Modern glass partitioned interior" style="background:radial-gradient(ellipse 50% 40% at 50% 35%,rgba(220,225,220,.8),rgba(220,225,220,0) 70%),linear-gradient(180deg,#bdb8aa,#8f8a7e 55%,#6a655c)"></div>
        <h3>Design Flexibility</h3>
        <p>Lorem ipsum dolor sit amet, consectetuer adipiscing elit, sed diam nonummy ni tincidunt ut laoreet dolore magna</p>
        <a class="more">Read More &gt;&gt;</a>
      </div>
      <div class="card">
        <div class="pic" role="img" aria-label="Apartment building surrounded by trees" style="background:radial-gradient(ellipse 40% 50% at 75% 45%,rgba(190,150,95,.85),rgba(190,150,95,0) 70%),linear-gradient(160deg,#7fb24e,#4e7d34 55%,#3a5f28)"></div>
        <h3>Environmentally Friendly</h3>
        <p>Lorem ipsum dolor sit amet, consectetuer adipiscing elit, sed diam nonummy ni tincidunt ut laoreet dolore magna</p>
        <a class="more">Read More &gt;&gt;</a>
      </div>
      <div class="card">
        <div class="pic" role="img" aria-label="Row of brick townhouses with front gardens" style="background:linear-gradient(180deg,#c4d6ea 0%,#b9a08c 30%,#9a6a52 55%,#6f8a45 80%,#4f6e33 100%)"></div>
        <h3>A Quieter Home</h3>
        <p>Lorem ipsum dolor sit amet, consectetuer adipiscing elit, sed diam nonummy ni tincidunt ut laoreet dolore magna</p>
        <a class="more">Read More &gt;&gt;</a>
      </div>
    </div>
  </div>
  <svg class="arrow l" width="12" height="24" viewBox="0 0 12 24"><path d="M11 1 L1 12 L11 23" stroke="#fff" stroke-width="2" fill="none"/></svg>
  <svg class="arrow r" width="12" height="24" viewBox="0 0 12 24"><path d="M1 1 L11 12 L1 23" stroke="#fff" stroke-width="2" fill="none"/></svg>
</section>

<section class="gallery-head center">
  <h2 class="heading"><span class="hl">Photo</span> Gallery</h2>
  <div class="divider"><i></i><b></b><i></i></div>
</section>
<section class="grid" aria-label="Photo gallery">
  <div role="img" aria-label="Engineer in orange hard hat with clipboard" style="background:radial-gradient(ellipse 35% 30% at 25% 20%,rgba(235,120,30,.85),rgba(235,120,30,0) 70%),radial-gradient(ellipse 55% 40% at 40% 90%,rgba(45,45,50,.8),rgba(45,45,50,0) 70%),linear-gradient(135deg,#f4f2ee,#e6dccd)"></div>
  <div role="img" aria-label="Two tradesmen beside a work van" style="background:radial-gradient(ellipse 45% 40% at 35% 65%,rgba(40,50,70,.8),rgba(40,50,70,0) 70%),radial-gradient(ellipse 30% 45% at 80% 55%,rgba(225,228,232,.85),rgba(225,228,232,0) 70%),linear-gradient(180deg,#3d96cc,#2f76a8)"></div>
  <div role="img" aria-label="Worker laying insulation panels on site" style="background:radial-gradient(ellipse 30% 30% at 55% 25%,rgba(240,200,40,.85),rgba(240,200,40,0) 70%),linear-gradient(180deg,#d7e2ec 0%,#e3dccb 35%,#dcc08a 60%,#b48f55 100%)"></div>
  <div role="img" aria-label="Gloved hands fitting red roof tiles" style="background:radial-gradient(ellipse 30% 40% at 70% 65%,rgba(240,200,60,.85),rgba(240,200,60,0) 70%),linear-gradient(160deg,#de6038,#c1452c 55%,#8e2f20)"></div>
  <div role="img" aria-label="Worker carrying timber on shoulder" style="background:radial-gradient(ellipse 35% 35% at 60% 30%,rgba(240,200,40,.8),rgba(240,200,40,0) 70%),radial-gradient(ellipse 45% 40% at 80% 70%,rgba(150,60,45,.8),rgba(150,60,45,0) 70%),linear-gradient(135deg,#dccfb6,#b9a07c 55%,#8c6a4c)"></div>
  <div role="img" aria-label="Smiling tradesman holding a wrench" style="background:radial-gradient(ellipse 45% 40% at 45% 85%,rgba(35,35,35,.9),rgba(35,35,35,0) 70%),radial-gradient(ellipse 30% 30% at 45% 35%,rgba(210,170,140,.7),rgba(210,170,140,0) 70%),linear-gradient(135deg,#f4f4f4,#d5d5d5)"></div>
  <div role="img" aria-label="Panels stacked in a warehouse" style="background:radial-gradient(ellipse 50% 25% at 45% 70%,rgba(240,242,246,.9),rgba(240,242,246,0) 70%),linear-gradient(180deg,#25282c 0%,#4a4e54 45%,#8e949b 75%,#5e636a 100%)"></div>
  <div role="img" aria-label="Modern clad commercial building" style="background:radial-gradient(ellipse 50% 45% at 60% 60%,rgba(110,118,128,.85),rgba(110,118,128,0) 70%),linear-gradient(180deg,#cfdbe8 0%,#e6e9ec 40%,#9aa2ab 80%,#6d747c 100%)"></div>
</section>

<section class="testimonials">
  <div class="center">
    <h2 class="heading"><span class="hl">Client</span> Testimonials</h2>
    <div class="divider"><i></i><b></b><i></i></div>
  </div>
  <div class="avatars">
    <div class="avatar" role="img" aria-label="Client portrait" style="background:linear-gradient(135deg,#d8d8d8,#6b5a4e)"></div>
    <div class="avatar" role="img" aria-label="Client portrait" style="background:linear-gradient(135deg,#e6e6e6,#8a6d58)"></div>
    <div class="avatar" role="img" aria-label="Client portrait" style="background:linear-gradient(135deg,#f0d25a,#e8e2dc 50%,#222)"></div>
  </div>
  <div class="quote">
    <svg class="quote-mark" width="24" height="20" viewBox="0 0 24 20"><path fill="#cfcfcf" d="M0 20V11C0 4 3 1 9 0l1 3C6 4 5 6 5 9h5v11zM14 20V11c0-7 3-10 9-11l1 3c-4 1-5 3-5 6h5v11z"/></svg>
    Nemo enim ipsam voluptatem quia voluptas sit aspernatur aut odit aut fugit, sed quia consequuntur magni dolores eos qui ratione voluptatem sequi nesciunt sit amet ipsum bibendum magnam aliquam voluptiat enim ad minima veniam.
  </div>
  <div class="author">Herry Lipsum</div>
</section>

<footer class="footer">
  <div class="wrap">
    <div class="col-links">
      <h4>Quick Links</h4>
      <div class="link-cols">
        <ul>
          <li class="current">Home</li><li>About us</li><li>Marlow Fen Dwellings</li><li>What is a sip</li><li>Benefits</li><li>FAQs</li><li>Designs</li><li>Granny Flats</li>
        </ul>
        <ul>
          <li>Residential</li><li>Photo Gallery</li><li>Project management and custom design</li><li>Services</li><li>Site Assemblyvv</li><li>Kit Supply</li><li>Contact us</li>
        </ul>
      </div>
    </div>
    <div class="col-contact">
      <h4>Contact Information</h4>
      <ul class="contact-list">
        <li><svg width="14" height="18" viewBox="0 0 14 18"><path fill="#ccc" d="M7 0a7 7 0 0 0-7 7c0 5 7 11 7 11s7-6 7-11a7 7 0 0 0-7-7zm0 10a3 3 0 1 1 0-6 3 3 0 0 1 0 6z"/></svg><span>123 ,Lorem ipsum dolor sit amet, consectetuer.</span></li>
        <li><svg width="14" height="14" viewBox="0 0 24 24"><path fill="#ccc" d="M6.6 10.8a15 15 0 0 0 6.6 6.6l2.2-2.2c.3-.3.7-.4 1-.2 1.1.4 2.3.6 3.6.6.6 0 1 .4 1 1V20c0 .6-.4 1-1 1A17 17 0 0 1 3 4c0-.6.4-1 1-1h3.5c.6 0 1 .4 1 1 0 1.3.2 2.5.6 3.6.1.3 0 .7-.2 1z"/></svg><span>123.456.789</span></li>
        <li><svg width="14" height="14" viewBox="0 0 14 14"><rect x="3" y="0" width="8" height="4" fill="#ccc"/><rect x="0" y="5" width="14" height="6" fill="#ccc"/><rect x="3" y="9" width="8" height="5" fill="#ccc" stroke="#222"/></svg><span>123.456.7890</span></li>
        <li><svg width="14" height="11" viewBox="0 0 14 11"><rect x=".5" y=".5" width="13" height="10" fill="none" stroke="#ccc"/><path d="M.5 .5 L7 6 L13.5 .5" fill="none" stroke="#ccc"/></svg><span>info@kestranepanels.com</span></li>
      </ul>
    </div>
    <div class="col-form">
      <h4>Quick Contact</h4>
      <div class="form">
        <div class="field"><svg width="11" height="11" viewBox="0 0 12 12"><circle cx="6" cy="3.5" r="3" fill="#666"/><path d="M0 12c0-4 3-5 6-5s6 1 6 5z" fill="#666"/></svg>Name</div>
        <div class="field"><svg width="12" height="9" viewBox="0 0 14 11"><rect x=".5" y=".5" width="13" height="10" fill="none" stroke="#666"/><path d="M.5 .5 L7 6 L13.5 .5" fill="none" stroke="#666"/></svg>Email</div>
        <div class="field"><svg width="11" height="11" viewBox="0 0 14 14"><rect x="3" y="0" width="8" height="4" fill="#666"/><rect x="0" y="5" width="14" height="6" fill="#666"/></svg>Phone Number</div>
        <div class="field tall"><svg width="11" height="11" viewBox="0 0 12 12"><rect x=".5" y=".5" width="11" height="11" fill="none" stroke="#666"/><path d="M3 9 L9 3" stroke="#666"/></svg>Message</div>
        <div class="submit">SUBMIT</div>
      </div>
    </div>
  </div>
</footer>

<div class="bottombar">
  <div class="wrap">
    <span>© 2016 Kestrane Panels. All Rights Reserved.</span>
    <div class="social" aria-label="Social links"><span class="social-btn"></span><span class="social-btn"></span><span class="social-btn"></span><span class="social-btn"></span></div>
  </div>
</div>

</body>
</html>
```